female esthetician looking for an impact business card

I an an expert in skin care industry with high experience in NYC.I want my business card to look professional , an impact at first look. I do want a combination between white and gold . I believe the font will be great if is gold.. The Fonts are also important. MIRABELA COSTINA (SKIN CARE BOUTIQUE)

THIS SHOULD BE THE BUSINESS NAME, and should be placed on th eback of the card.
IN front m, the name MIRABELA COSTINA - ESTHETCIAN

BY APPOINTMENTS ONLY: 518.240.7136

Target Market(s)

HIGH END CLIENTELE

Contact Information for Business Card

iT WILL BE on a luxury paper. I neeed the wow feeling

Requirements
Should not have
• pictures

```html
<!DOCTYPE html>
<html lang="en">
<head>
<meta charset="utf-8">
<title>Mirabela Costina – Business Card</title>
<link rel="stylesheet" href="https://fonts.googleapis.com/css2?family=Cinzel:wght@400;500&family=Lato:wght@400&display=swap">
<style>
  :root {
    --backdrop: #2b2623;
    --card: #333333;
    --gold: #f2b40a;
    --rule: #6b6b6b;
  }
  * { margin: 0; padding: 0; box-sizing: border-box; }
  html, body {
    width: 1200px;
    height: 844px;
    overflow: hidden;
    background: var(--backdrop);
  }
  .canvas {
    position: relative;
    width: 1200px;
    height: 844px;
  }
  .card {
    position: absolute;
    top: 268px;
    width: 540px;
    height: 309px;
    background: var(--card);
    box-shadow: 0 10px 30px rgba(0, 0, 0, 0.45);
    color: var(--gold);
    display: flex;
    flex-direction: column;
    align-items: center;
    justify-content: center;
    text-align: center;
  }
  .card--front { left: 45px; }
  .card--back { left: 615px; }

  .person-name {
    font-family: "Cinzel", serif;
    font-weight: 500;
    font-size: 24px;
    letter-spacing: 0.02em;
    line-height: 1;
  }
  .person-title {
    font-family: "Cinzel", serif;
    font-size: 12px;
    letter-spacing: 0.06em;
    margin-top: 6px;
  }
  .divider {
    width: 220px;
    height: 1px;
    background: var(--rule);
    margin: 12px 0 14px;
  }
  .appointments {
    font-family: "Cinzel", serif;
    font-size: 15px;
    letter-spacing: 0.03em;
  }
  .contact {
    font-family: "Lato", sans-serif;
    font-size: 16px;
    line-height: 1.35;
    margin-top: 4px;
  }

  .brand-name {
    font-family: "Cinzel", serif;
    font-weight: 400;
    font-size: 33px;
    letter-spacing: 0.02em;
    line-height: 1;
  }
  .brand-tagline {
    font-family: "Cinzel", serif;
    font-weight: 400;
    font-size: 11px;
    letter-spacing: 0.42em;
    margin-top: 6px;
  }
</style>
</head>
<body>
<main class="canvas">
  <section class="card card--front" aria-label="Card front">
    <h1 class="person-name">Mirabela Costina</h1>
    <p class="person-title">Esthetcian</p>
    <div class="divider"></div>
    <p class="appointments">By Appointments Only</p>
    <p class="contact">518.240.7136<br>mirabelacostina@mail.com</p>
  </section>

  <section class="card card--back" aria-label="Card back">
    <h2 class="brand-name">Mirabela Costina</h2>
    <p class="brand-tagline">Skin Care Boutique</p>
  </section>
</main>
</body>
</html>
```